Audio and Video download site

I am looking for a good and beautiful website where users can be a able to download and upload musicial files and video file. Basically, there will be two categories. The first category for the music files( mp3, mva and other popular music files) while the second category will be for video files (mp4, wmv, divx and other files) users would be able to like and dislike a song/video. Users do not necessarily have to sign up for them to make you or download and upload files from the website. The website should be youthful.

```html
<!DOCTYPE html>
<html lang="en">
<head>
<meta charset="utf-8">
<title>VibeNest — Music &amp; Video</title>
<link href="https://fonts.googleapis.com/css2?family=Quicksand:wght@300;400;500&display=swap" rel="stylesheet">
<style>
:root{
  --wine:#7a0a1a;
  --ink:#0d0d0d;
  --paper:#f6f6f6;
  --white:#ffffff;
  --hero-a:#5d6a6e;
  --hero-b:#8b8e88;
  --hero-c:#3f4a4c;
}
*{margin:0;padding:0;box-sizing:border-box}
html,body{width:688px;height:1200px;overflow:hidden}
body{font-family:'Quicksand',sans-serif;background:var(--ink);color:var(--white);position:relative}
.abs{position:absolute}

/* hero */
.hero{left:0;top:0;width:688px;height:554px;background:linear-gradient(120deg,var(--hero-c) 0%,var(--hero-a) 35%,var(--hero-b) 65%,#6f6a5f 100%)}
.player-shade{left:0;top:31px;width:445px;height:491px;background:rgba(40,46,48,.45)}
.list-shade{left:449px;top:31px;width:239px;height:491px;background:rgba(40,46,48,.25)}
.divider{left:445px;top:31px;width:4px;height:491px;background:rgba(230,230,230,.6)}
.topbar{top:14px;font-size:12.5px;font-weight:400}
.album{left:12px;top:44px;width:421px;height:421px;border:1px solid rgba(0,0,0,.55);border-radius:3px}
.album-msg{left:0;right:0;top:191px;text-align:center;font-size:24px;font-weight:400}
.time{left:17px;top:450px;font-size:10px}
.progress{left:50px;top:454px;width:378px;height:7px;border-radius:4px;background:var(--wine)}
.controls{left:0;top:468px;width:445px;height:50px}

.brand{right:58px;top:39px;font-size:34px;font-weight:300;letter-spacing:1px;line-height:44px}
.brand-dot{left:642px;top:48px;width:24px;height:24px;border-radius:50%;background:var(--wine)}
.playlist{left:463px;top:91px;width:212px;height:415px;border:1px solid rgba(0,0,0,.55);border-radius:3px;text-align:center}
.playlist p{font-size:16px;line-height:20px}
.playlist a{color:var(--white);font-size:16px;line-height:20px;display:block}
.handle{left:453px;width:6px;height:6px;background:#1c1c1c}

/* now playing strip */
.listening{top:554px;left:0;width:688px;height:277px;background:var(--ink)}
.listening h2{position:absolute;top:16px;left:0;right:0;text-align:center;font-size:19px;font-weight:300;letter-spacing:1.5px}
.tile{top:65px;width:164px;height:163px}
.caption{top:236px;font-size:12.5px;white-space:nowrap}
.nav-arrow{top:99px;width:33px;height:120px;background:rgba(255,255,255,.35)}

/* video promo */
.promo{top:831px;left:0;width:688px;height:224px;background:radial-gradient(ellipse at 30% 20%,#ffffff 0%,var(--paper) 60%,#ececec 100%);color:var(--wine)}
.promo h2{position:absolute;left:27px;top:78px;font-size:38px;font-weight:300;line-height:35px;letter-spacing:3px}
.promo p{position:absolute;left:27px;top:168px;font-size:22px;font-weight:400;color:#1a1a1a;letter-spacing:2.7px}

/* join */
.join{top:1055px;left:0;width:688px;height:145px;background:#000}
.join-box{left:9px;top:0;width:669px;height:113px;border:1px solid #bbb;border-top:none;border-radius:0 0 4px 4px}
.join h3{position:absolute;right:20px;top:10px;font-size:19px;font-weight:300;color:var(--wine)}
.join .lead{position:absolute;right:20px;top:32px;font-size:11px;letter-spacing:.6px}
.btn{position:absolute;left:559px;top:50px;width:106px;height:31px;background:var(--wine);color:#b01c2e;font-size:12px;text-align:center;line-height:31px;border-radius:2px}
.signin{position:absolute;right:23px;top:89px;font-size:10px}
.signin a{color:var(--white)}
.legal{top:1176px;left:0;width:688px;text-align:center;font-size:6.5px;line-height:8px;font-weight:500}
.legal a{color:var(--white)}
</style>
</head>
<body>

<div class="abs hero" role="img" aria-label="Photo of a person with headphones in a café, used as page backdrop"></div>
<div class="abs player-shade"></div>
<div class="abs list-shade"></div>
<div class="abs divider"></div>

<span class="abs topbar" style="left:443px">Signed in as <em>GUEST</em></span>
<span class="abs topbar" style="left:579px">Log In</span>
<span class="abs topbar" style="left:637px">Register</span>

<section class="abs album">
  <p class="abs album-msg">Album art not available.</p>
</section>
<span class="abs time">00:00</span>
<div class="abs progress"></div>

<svg class="abs controls" viewBox="0 0 445 50" aria-label="Player controls">
  <rect x="27" y="16" width="5" height="20" fill="#7a0a1a"/>
  <polygon points="32,22 39,14 39,38 32,30" fill="#7a0a1a"/>
  <polygon points="160,14 146,25 160,36" fill="#7a0a1a"/>
  <polygon points="174,14 160,25 174,36" fill="#7a0a1a"/>
  <circle cx="221" cy="25" r="22" fill="#7a0a1a"/>
  <polygon points="213,13 213,37 233,25" fill="#111"/>
  <polygon points="269,14 283,25 269,36" fill="#7a0a1a"/>
  <polygon points="283,14 297,25 283,36" fill="#7a0a1a"/>
  <path d="M356 19 h5 q5 0 8 6 q3 6 8 6 h5 M356 31 h5 q5 0 8 -6 q3 -6 8 -6 h5" fill="none" stroke="#7a0a1a" stroke-width="2"/>
  <polygon points="382,15 386,19 382,23" fill="#7a0a1a"/>
  <polygon points="382,27 386,31 382,35" fill="#7a0a1a"/>
  <rect x="402" y="12" width="8" height="14" fill="#7a0a1a"/>
  <polygon points="396,26 416,26 406,38" fill="#7a0a1a"/>
</svg>

<div class="abs brand">VibeNest</div>
<div class="abs brand-dot"></div>

<section class="abs playlist">
  <div style="margin-top:110px">
    <p>Oh no!</p>
    <p>Your playlist is empty.</p>
    <a href="#" style="margin-top:18px">Upload your music now</a>
    <p>or</p>
    <a href="#">browse through our library</a>
  </div>
</section>
<div class="abs handle" style="top:285px"></div>
<div class="abs handle" style="top:296px"></div>
<div class="abs handle" style="top:307px"></div>

<section class="abs listening">
  <h2>Hear what others are listening to right now</h2>
  <div class="abs tile" style="left:0;background:linear-gradient(135deg,#dcdcdc,#f4f4f4)" role="img" aria-label="Album cover: Novaro, Summer Drift"></div>
  <div class="abs tile" style="left:174px;background:linear-gradient(90deg,#e39a3a,#2a2030 45%,#3a2a40 60%,#d46fa8)" role="img" aria-label="Album cover: Lumento, Honey Static"></div>
  <div class="abs tile" style="left:348px;background:linear-gradient(180deg,#3d6fb0 0%,#6d8fb0 50%,#5a8a3a 100%)" role="img" aria-label="Album cover: Kestrel and Mae Lin, Long Way Back"></div>
  <div class="abs tile" style="left:523px;width:165px;background:#f7f7f7" role="img" aria-label="Album cover: Harbor, The Chemist"></div>
  <div class="abs nav-arrow" style="left:0"></div>
  <div class="abs nav-arrow" style="left:655px"></div>
  <svg class="abs" style="left:0;top:103px" width="33" height="112"><polygon points="24,4 24,108 6,56" fill="rgba(255,255,255,.6)"/></svg>
  <svg class="abs" style="left:655px;top:103px" width="33" height="112"><polygon points="9,4 9,108 27,56" fill="rgba(255,255,255,.6)"/></svg>
  <span class="abs caption" style="left:7px">Novaro - Summer Drift ...</span>
  <span class="abs caption" style="left:176px">Lumento - Honey Static ...</span>
  <span class="abs caption" style="left:352px">Kestrel and Mae Lin - Lo ...</span>
  <span class="abs caption" style="left:540px">Harbor - The Chemist</span>
</section>

<section class="abs promo">
  <h2>Want to watch<br>a video instead?</h2>
  <p>Check out our video section!</p>
  <svg class="abs" style="left:490px;top:40px" width="160" height="150" aria-label="Play">
    <polygon points="14,112 155,105 14,140" fill="rgba(0,0,0,.06)"/>
    <polygon points="5,3 124,72 5,140" fill="#7a0a1a"/>
  </svg>
</section>

<section class="abs join">
  <div class="abs join-box"></div>
  <h3>Tired of creating a new playlist every time you visit?</h3>
  <p class="lead">Join in and save your playlist, upload your music, or download somebody else's jam.</p>
  <div class="btn">Create account</div>
  <p class="signin">Already have an account? <a href="#">Sign in</a>.</p>
</section>
<p class="abs legal">Copyright © 2016 VibeNest. Use of this website constitutes acceptance of our<br><a href="#">User Agreement</a> and <a href="#">Privacy Policy</a>.</p>

</body>
</html>
```